Business cards in digital learning for freelancer

Hello, I need a business cards in french. I work in the Digital learning industries as freeelancer; I'm an expert in digital learning. I work in France. My customer are in the health industry, pharmaceutical industry, and training organization. I've got a logo. I offer three services: consulting, Design, and Training. In the consulting, I offers coaching to choose your digital learning tools and the digital learning strategy. For the Design, I product differents level of elearning like rapid-learning, elearning, micro-learning, video-learning. And for the training service, I've create training about pedagogy, digital learning management project, Digital learning design.
I join my Logo create in this platform. My universe is gamified. I like the life, and I'm very social. I want a card like I'm I. I love Art (painting), Europeen comics. I use in my visual support "permanent maker" font and caracters. I would like cards: elegant, modern, Top class. If you need any information, you can ask me.
thanks for ideas

Target Market(s)

in health industries and training organization for Training manager, instructor, human resources director

Contact Information for Business Card

Phone number : 06 71 38 95 14 , mail: bastiengolmier@quelmoto.fr, web: bastiengolmier.fr , Carrivo

Font styles to use
Sans Serif

Requirements
Must have
• Use my logo and write my 3 services (consulting, training, design)

```html
<!DOCTYPE html>
<html lang="fr">
<head>
<meta charset="utf-8">
<title>Golmier – cartes de visite</title>
<link rel="stylesheet" href="https://fonts.googleapis.com/css2?family=Arimo:wght@400;700&family=Cinzel:wght@400;600&display=swap">
<style>
  :root {
    --stage: #2b2b2d;
    --card: #1c1d1f;
    --orange: #f47a20;
    --grey-light: #d6d6d6;
    --grey-mid: #8a8a8a;
    --rule: #6d6d6d;
  }
  * { box-sizing: border-box; margin: 0; padding: 0; }
  html, body {
    width: 1200px; height: 1108px; overflow: hidden;
    background: var(--stage);
  }
  .stage {
    position: relative; width: 1200px; height: 1108px;
  }
  .card {
    position: absolute; top: 229px;
    width: 420px; height: 650px;
    background: var(--card);
    border-radius: 22px;
    box-shadow: 0 18px 40px rgba(0,0,0,.45);
  }
  .card--front { left: 150px; text-align: center; }
  .card--back { left: 630px; }

  .brand {
    margin-top: 160px;
    font-family: "Arimo", sans-serif; font-weight: 700;
    font-size: 58px; letter-spacing: 2px; color: var(--orange);
    line-height: 1;
  }
  .tagline {
    display: flex; align-items: center; justify-content: center; gap: 12px;
    margin-top: 12px;
    font-family: "Cinzel", serif; font-size: 15px; letter-spacing: 2px;
    color: var(--grey-mid);
  }
  .tagline::before, .tagline::after {
    content: ""; width: 70px; height: 1px; background: var(--rule);
  }
  .services {
    margin-top: 16px;
    font-family: "Arimo", sans-serif; font-size: 17px;
    color: var(--grey-light); letter-spacing: .5px;
  }
  .services .dot {
    display: inline-block; width: 9px; height: 9px; border-radius: 50%;
    background: var(--orange); margin: 0 8px; vertical-align: middle;
  }
  .person-name {
    margin-top: 70px;
    font-family: "Cinzel", serif; font-weight: 600;
    font-size: 28px; color: var(--orange); letter-spacing: 1px;
  }
  .person-role {
    margin-top: 4px;
    font-family: "Arimo", sans-serif; font-size: 18px; color: var(--grey-light);
  }
  .icon-row {
    display: flex; align-items: center; justify-content: center; gap: 8px;
    margin-top: 22px;
  }
  .icon-row::before, .icon-row::after {
    content: ""; width: 70px; height: 1px; background: var(--rule); margin: 0 8px;
  }
  .icon {
    width: 32px; height: 32px; border-radius: 6px; background: var(--orange);
    display: flex; align-items: center; justify-content: center;
  }
  .contact {
    margin-top: 14px;
    font-family: "Arimo", sans-serif; font-size: 18px; line-height: 1.4;
    color: var(--grey-light);
  }
  .network {
    display: flex; align-items: center; justify-content: center; gap: 10px;
    margin-top: 20px;
    font-family: "Arimo", sans-serif; font-weight: 700; font-size: 16px;
    color: var(--orange);
  }
  .network::before, .network::after {
    content: ""; width: 80px; height: 1px; background: var(--rule); margin: 0 6px;
  }
  .network .mark {
    width: 14px; height: 14px; border-radius: 50%; background: var(--orange);
  }

  .back-brand {
    position: absolute; left: 0; right: 0; top: 400px; text-align: center;
    font-family: "Arimo", sans-serif; font-weight: 700; font-size: 26px;
    letter-spacing: 1px; color: var(--orange);
  }
</style>
</head>
<body>
<main class="stage">
  <section class="card card--front">
    <div class="brand">GOLMIER</div>
    <div class="tagline">DIGITAL LEARNING</div>
    <div class="services">CONSULTING<span class="dot"></span>TRAINING<span class="dot"></span>DESIGN</div>

    <div class="person-name">BASTIEN GOLMIER</div>
    <div class="person-role">Managing Director</div>

    <div class="icon-row">
      <span class="icon" aria-label="Téléphone">
        <svg width="20" height="20" viewBox="0 0 24 24"><path fill="#1c1d1f" d="M6.6 10.8a15 15 0 0 0 6.6 6.6l2.2-2.2a1 1 0 0 1 1-.25 11.4 11.4 0 0 0 3.6.57 1 1 0 0 1 1 1V20a1 1 0 0 1-1 1A17 17 0 0 1 3 4a1 1 0 0 1 1-1h3.5a1 1 0 0 1 1 1c0 1.25.2 2.45.57 3.57a1 1 0 0 1-.25 1z"/></svg>
      </span>
      <span class="icon" aria-label="E-mail">
        <svg width="20" height="20" viewBox="0 0 24 24"><rect x="3" y="6" width="18" height="12" fill="none" stroke="#1c1d1f" stroke-width="2"/><path d="M3 6l9 7 9-7M3 18l7-6M21 18l-7-6" fill="none" stroke="#1c1d1f" stroke-width="1.6"/></svg>
      </span>
      <span class="icon" aria-label="Site web">
        <svg width="20" height="20" viewBox="0 0 24 24"><circle cx="12" cy="12" r="8.5" fill="none" stroke="#1c1d1f" stroke-width="2"/><path d="M3.5 12h17M12 3.5c3 3 3 14 0 17M12 3.5c-3 3-3 14 0 17" fill="none" stroke="#1c1d1f" stroke-width="1.5"/></svg>
      </span>
    </div>

    <div class="contact">
      <div>06 71 38 95 14</div>
      <div>bastiengolmier@quelmoto.fr</div>
      <div>www.bastiengolmier.fr</div>
    </div>

    <div class="network"><span class="mark"></span>Carrivo</div>
  </section>

  <section class="card card--back">
    <div class="back-brand">GOLMIER</div>
  </section>
</main>
</body>
</html>
```